Awesome business card design needed

We need a new business card design to go with our new logo.
We are a web development agency that specialises in highly complex back-end integrations as opposed to design, our customers are retailers, hotels, hospitals and any other organisation that has a large online marketing department.
Take a look at our website - www.brenoloft.com for some inspiration.
We want our new business cards to exude class, professionalism and style.
We are likely to choose a high-end card to print them on but we want the design of the card itself to really turn heads.
We have no specific colour requirements, the logo as you will see is a turquoise colour R89 G171 B167 #59aba7 but it can also be in white if you want to make the colour of the card something different.
The information on the card should be:
Name
Position
Tel
email
Potentially a double sided card could have our web address, twitter and FB links.

```html
<!DOCTYPE html>
<html lang="en">
<head>
<meta charset="utf-8">
<title>Brenoloft business card</title>
<link href="https://fonts.googleapis.com/css2?family=Saira:wght@400;600;700;800&display=swap" rel="stylesheet">
<style>
  :root {
    --teal: #59aba7;
    --ink: #3d3f42;
    --rule: #333538;
    --card: #ffffff;
    --backdrop: #c9915f;
  }
  * { margin: 0; padding: 0; box-sizing: border-box; }
  html, body { width: 1194px; height: 1200px; overflow: hidden; }
  body {
    background: var(--backdrop);
    font-family: "Saira", sans-serif;
    position: relative;
  }
  .card {
    position: absolute;
    background: var(--card);
    overflow: hidden;
  }
  .card-front {
    left: 37px; top: 32px; width: 971px; height: 555px;
    border-radius: 56px 0 56px 0;
  }
  .card-back {
    left: 187px; top: 608px; width: 969px; height: 553px;
    border-radius: 56px 0 56px 0;
    border: 1px solid #3a3a3a;
  }
  .wordmark {
    position: absolute; left: 0; right: 0;
    text-align: center;
    font-family: "Saira", sans-serif;
    font-weight: 600;
    color: var(--teal);
    font-size: 138px;
    line-height: 1;
    letter-spacing: 2px;
  }
  .card-front .wordmark { top: 92px; }
  .card-back .wordmark { top: 128px; }
  .person {
    position: absolute; left: 0; right: 0; top: 326px;
    text-align: center;
    font-size: 31px; line-height: 1;
  }
  .person-name { font-weight: 800; color: var(--ink); }
  .person-role { font-weight: 400; color: var(--teal); font-size: 27px; }
  .divider-rule {
    position: absolute; left: 0; right: 0; top: 382px;
    height: 4px; background: var(--rule);
  }
  .contact-band {
    position: absolute; left: 0; right: 0; top: 391px; bottom: 0;
    background: var(--teal);
    color: #fff;
    font-size: 26px;
    line-height: 39px;
  }
  .address {
    position: absolute; right: 562px; top: 30px;
    text-align: right;
  }
  .band-divider {
    position: absolute; left: 436px; top: 26px; width: 2px; height: 130px;
    background: rgba(255,255,255,0.55);
  }
  .reach {
    position: absolute; left: 459px; top: 30px;
    list-style: none;
  }
  .reach li { display: flex; align-items: center; gap: 12px; }
  .reach svg { width: 24px; height: 24px; flex: none; }
  .follow {
    position: absolute; left: 0; right: 0; top: 444px - 0px;
  }
  .follow-row {
    position: absolute; left: 0; right: 0; top: 376px;
    display: flex; justify-content: center; align-items: center; gap: 22px;
  }
  .follow-label {
    font-weight: 800; font-size: 32px; color: var(--teal);
    letter-spacing: 1px; margin-right: 2px;
  }
  .social-tile {
    width: 56px; height: 56px; border-radius: 10px;
    background: var(--teal);
  }
  .social-tile.alt { background: #4a6fa8; }
  .site-url {
    position: absolute; left: 0; right: 0; top: 452px;
    text-align: center;
    font-size: 29px; letter-spacing: 4px; color: var(--ink);
  }
  .site-url strong { color: var(--teal); font-weight: 700; }
</style>
</head>
<body>

<section class="card card-front">
  <div class="wordmark">brenoloft</div>
  <p class="person"><span class="person-name">Your Name,</span> <span class="person-role">Position</span></p>
  <div class="divider-rule"></div>
  <div class="contact-band">
    <address class="address" style="font-style:normal">
      Street Name<br>City Name<br>State Zip Code
    </address>
    <div class="band-divider"></div>
    <ul class="reach">
      <li>
        <svg viewBox="0 0 24 24" fill="none" stroke="#fff" stroke-width="1.6">
          <circle cx="12" cy="12" r="10.5"/>
          <path d="M9 6.5l2 3-1.3 1.2c.6 1.5 1.9 2.8 3.4 3.5l1.2-1.3 3 2-1.2 2.1c-4.4-.3-8.8-4.6-9.1-9.1z" fill="#fff" stroke="none"/>
        </svg>123-456-7890
      </li>
      <li>
        <svg viewBox="0 0 24 24" fill="none" stroke="#fff" stroke-width="1.6">
          <rect x="2.5" y="8" width="19" height="12" fill="#fff" stroke="none"/>
          <path d="M2.5 8l9.5 7 9.5-7" stroke="var(--teal)"/>
          <path d="M2.5 8L12 3l9.5 5" />
        </svg>info@brenoloft.com
      </li>
      <li>
        <svg viewBox="0 0 24 24" fill="none" stroke="#fff" stroke-width="1.4">
          <circle cx="12" cy="12" r="10"/>
          <ellipse cx="12" cy="12" rx="4.5" ry="10"/>
          <path d="M2 12h20M4 6.5h16M4 17.5h16"/>
        </svg>www.brenoloft.com
      </li>
    </ul>
  </div>
</section>

<section class="card card-back">
  <div class="wordmark">brenoloft</div>
  <div class="follow-row">
    <span class="follow-label">Follow Us On:</span>
    <span class="social-tile" role="img" aria-label="Social network link"></span>
    <span class="social-tile alt" role="img" aria-label="Social network link"></span>
  </div>
  <p class="site-url">www.<strong>brenoloft</strong>.com</p>
</section>

</body>
</html>
```